Quorbelline.io - Please redesign to make it look better from current design

We already have the current website, that you can access but we think it can improve from current version.
Quorbelline is a cryptocurrency hedge fund that allow you to participate in the hedge fund with cryptocurrency such as eth.
At current phase, we are doing an ICO, then we want to make sure that the website it looks professional, beautiful and trustable enough for investors after looking at our website.
Target Market(s)
Investors
Industry/Entity Type
Investment
Coding
Coded - Design and coding required
Number of Pages Required
1 page
Look and feel
Each slider illustrates characteristics of the customer's brand and the style your logo design should communicate.

```html
<!DOCTYPE html>
<html lang="en">
<head>
<meta charset="utf-8">
<title>Quorbelline.io – Digital Asset Management</title>
<link rel="stylesheet" href="https://fonts.googleapis.com/css2?family=Open+Sans:ital,wght@0,400;0,600;0,700;1,400&family=Roboto:wght@300;400&display=swap">
<style>
:root{
  --navy:#15237f;
  --navy-deep:#0d1a66;
  --ice:#cdeefe;
  --ink:#222;
  --muted:#555;
  --grey-band:#eeeeee;
  --white:#fff;
  --rule:#d9d9d9;
}
*{box-sizing:border-box;margin:0;padding:0}
html,body{width:1200px;height:2980px;overflow:hidden}
body{position:relative;background:var(--white);font-family:"Open Sans",Arial,sans-serif;color:var(--ink)}
.abs{position:absolute}
.heading-light{font-family:"Roboto",Arial,sans-serif;font-weight:300}

/* header */
.brand{left:80px;top:18px;display:flex;align-items:center;gap:12px}
.brand-dot{width:40px;height:40px;border-radius:50%;background:var(--navy)}
.brand-name{font-weight:600;color:var(--navy);font-size:20px}
.nav{left:638px;top:52px;display:flex;gap:46px;font-size:16px;color:#111}
.nav a{color:inherit;text-decoration:none}

/* hero */
.hero-title{left:78px;top:245px;font-size:84px;color:var(--navy);letter-spacing:1px}
.hero-sub{left:80px;top:356px;font-size:38px;color:var(--navy)}
.hero-rule{left:80px;top:434px;width:64px;height:2px;background:var(--navy)}
.hero-text{left:80px;top:462px;width:530px;font-size:18px;line-height:26px;color:#444}
.hero-art{left:620px;top:120px;width:580px;height:556px;border-radius:8px 0 0 0;
  background:
    radial-gradient(circle at 30% 25%,rgba(21,35,127,.22) 0,rgba(21,35,127,0) 38%),
    radial-gradient(circle at 75% 60%,rgba(21,35,127,.28) 0,rgba(21,35,127,0) 42%),
    linear-gradient(160deg,#eef1fb 0%,#d6ddf3 55%,#c3cdee 100%)}

/* about */
.band-navy{left:0;width:1200px;background:var(--navy)}
.about-art{left:78px;top:735px;width:480px;height:385px;border-radius:6px;
  background:
    linear-gradient(180deg,rgba(255,255,255,0) 0,rgba(255,255,255,0) 78%,#d4d4d4 78%,#a9a9a9 100%),
    radial-gradient(ellipse at 50% 45%,#2c6fe0 0%,#1546b0 45%,#0a2277 100%);
  box-shadow:0 0 0 8px #1c1c1c inset}
.section-title{font-size:40px;color:var(--white)}
.about-text{left:626px;top:792px;width:480px;font-size:15px;line-height:25px;color:var(--white)}
.btn{display:flex;align-items:center;justify-content:center;width:166px;height:52px;background:var(--ice);color:var(--navy);font-weight:700;font-size:14px;text-transform:uppercase}

/* team */
.team-band{left:0;top:1134px;width:1200px;height:565px;background:var(--grey-band)}
.team-title{left:0;top:1180px;width:1200px;text-align:center;font-size:40px;color:#111}
.card{top:1263px;width:320px;height:382px;background:var(--white);box-shadow:0 2px 6px rgba(0,0,0,.15)}
.card-head{display:flex;align-items:center;gap:18px;height:120px;padding:0 10px;border-bottom:1px solid var(--rule)}
.card-photo{flex:none;width:88px;height:88px;border-radius:50%;background:radial-gradient(circle at 50% 40%,#c9a98f 0%,#8a6a57 45%,#2f3340 100%)}
.card-role{font-style:italic;font-size:15px;color:#333}
.card-name{font-size:17px;color:var(--navy);margin-top:4px;white-space:nowrap}
.card-body{padding:20px 10px 0 12px;font-size:15px;line-height:25px;color:#444}

/* process */
.process-sub{left:80px;top:1832px;font-size:30px;color:var(--white)}
.process-text{left:80px;top:1885px;width:520px;font-size:16px;line-height:26px;color:var(--white)}
.process-art{left:646px;top:1760px;width:440px;height:312px;border-radius:4px;
  background:
    linear-gradient(180deg,rgba(0,0,0,0) 0,rgba(0,0,0,0) 74%,#5a5a5a 74%,#2e2e2e 100%),
    linear-gradient(90deg,#f6d9b8 0%,#f1f1f1 30%,#ffffff 60%,#e7ebf6 100%);
  box-shadow:0 0 0 10px #2f2f2f inset}

/* distribution */
.dist-title{left:0;top:2160px;width:1200px;text-align:center;font-size:28px;color:var(--navy);font-weight:400}
.dist-center{left:0;top:2215px;width:1200px;text-align:center;color:#333}
.dist-center .big{font-size:22px}
.dist-center .small{font-size:14px}
.tier{font-size:22px;color:#333;white-space:nowrap}
.tier small{font-size:15px}
.tier span{display:block;font-size:14px;margin-top:-2px}
.dist-note{left:0;top:2548px;width:1200px;text-align:center;font-size:17px;color:#333}

/* footer */
.footer{left:0;top:2627px;width:1200px;height:353px;background:var(--navy)}
.f-head{font-size:19px;color:var(--white);text-transform:uppercase;font-weight:400}
.f-text{font-size:15px;line-height:25px;color:var(--white)}
.newsletter-field{left:640px;top:2794px;width:272px;height:52px;background:var(--white);display:flex;align-items:center;padding-left:24px;font-size:13px;color:#888}
.newsletter-send{left:860px;top:2794px;width:52px;height:52px;background:var(--ice);display:flex;align-items:center;justify-content:center}
.f-brand{left:953px;top:2660px;width:150px;text-align:center}
.f-brand-dot{width:120px;height:120px;border-radius:50%;background:var(--white);margin:0 auto 8px}
.f-brand-name{font-weight:600;color:var(--white);font-size:16px}
.social{top:2824px;width:38px;height:38px;border-radius:50%;background:var(--ice)}
.f-rule{left:80px;top:2920px;width:1040px;height:1px;background:rgba(255,255,255,.25)}
.copyright{left:0;top:2942px;width:1200px;text-align:center;font-size:15px;color:var(--white)}
</style>
</head>
<body>

<header>
  <div class="abs brand"><span class="brand-dot"></span><span class="brand-name">quorbelline</span></div>
  <nav class="abs nav"><a href="#">Home</a><a href="#">About</a><a href="#">Process</a><a href="#">Our Team</a><a href="#">Contact</a></nav>
</header>

<section class="hero">
  <h1 class="abs hero-title heading-light">quorbelline</h1>
  <p class="abs hero-sub heading-light">Digital Asset Management</p>
  <div class="abs hero-rule"></div>
  <p class="abs hero-text">Quorbelline enable companies and investors to facilities business operation in modern digital world, including asset management on hedge fund strategy model.</p>
  <div class="abs hero-art" role="img" aria-label="Line illustration of crypto assets: coin, rocket, bar chart, wallet and payment card connected by nodes"></div>
</section>

<section class="abs band-navy" style="top:676px;height:458px"></section>
<div class="abs about-art" role="img" aria-label="Desktop monitor showing a blue trading chart"></div>
<h2 class="abs section-title heading-light" style="left:626px;top:728px">ABOUT US</h2>
<p class="abs about-text">Quorbelline process and manages on hedge fund strategy models which invests in a diversified portfolio of blockchain tokens. Blockchain tokens are emerging which add a monetary incentive layer to p2p protocols and facilitate equity crowdfunding that anyone in the world can participate in. This means open source software developers can monetize their networks at the protocol level and users of the network are the equity owners of the network. For this conditions, returns will go to holders of the tokens.</p>
<a class="abs btn" style="left:626px;top:1032px">Explore More</a>

<section class="abs team-band"></section>
<h2 class="abs team-title heading-light">EXECUTIVE TEAM</h2>

<article class="abs card" style="left:80px">
  <div class="card-head"><div class="card-photo" role="img" aria-label="Portrait photo of the director"></div><div><div class="card-role">Director</div><div class="card-name">Varin Lomtaweekul</div></div></div>
  <p class="card-body">As a hedge fund manager. Lomtaweekul is the Chief Executive Officer of Harrowgate Capital LLC, an investment manager of Ironvale Fund SP (Long-Short Equity Fund, investing in U.S. Stock Market) and Kaizen Delta Fund (Managed Futures Fund, focusing in Japanese Futures Market) Both based in Tokyo.</p>
</article>
<article class="abs card" style="left:440px">
  <div class="card-head"><div class="card-photo" role="img" aria-label="Portrait photo of the technical advisor"></div><div><div class="card-role">Technical advisor</div><div class="card-name">Kittipat Sornsuk</div></div></div>
  <p class="card-body">Sornsuk has various experienced on cryptocurrency and blockchain technology. He created what was the world's 4th most valuable cryptocurrency in February 2014. He is also the world's first person to implement stealth addresses in Vellum Wallets, improving cryptocurrency anonymity.</p>
</article>
<article class="abs card" style="left:800px">
  <div class="card-head"><div class="card-photo" role="img" aria-label="Portrait photo of the marketing consultant"></div><div><div class="card-role">Marketing Consultant</div><div class="card-name">Nattapong Chaiwerapan</div></div></div>
  <p class="card-body">Chaiwerapan embeds a decade of experience in brand building, strategic planning, and marketing communication across the global agencies, such as Brightline Group, Norcross, Palewood, Tessary. His seasoned specialty focuses on exploring a new market insight to formulate disruptive strategies</p>
</article>

<section class="abs band-navy" style="top:1699px;height:417px"></section>
<h2 class="abs section-title heading-light" style="left:80px;top:1745px">PROCESS</h2>
<h3 class="abs process-sub heading-light">Hedge Fund Model</h3>
<p class="abs process-text">Quorbelline run on closed-end fund (CEF) model which offers its shares to investors and utilize the fund to speculate and invest in the innovative blockchain tokens. Quorbelline will charge an upfront annual operation fee 4% of the money raised during the ICO. After that, the fund will charge a quarterly performance of 50% on the net profit made.</p>
<div class="abs process-art" role="img" aria-label="Cartoon illustration of a presenter pointing at a laptop showing a crypto markets table"></div>

<h2 class="abs dist-title">Net Profit Distribution</h2>
<div class="abs dist-center"><div class="big">50 %</div><div class="small">of net profit is distributed to investors</div></div>

<svg class="abs" style="left:0;top:2260px" width="1200" height="280" viewBox="0 0 1200 280" aria-hidden="true">
  <g stroke="#ddd" stroke-width="1.5" fill="none">
    <line x1="600" y1="30" x2="600" y2="66"/>
    <line x1="190" y1="84" x2="1010" y2="84"/>
    <polyline points="430,84 510,132"/>
    <polyline points="770,84 690,132"/>
    <polyline points="240,250 440,250 545,218"/>
    <polyline points="960,250 760,250 655,218"/>
  </g>
  <polygon points="600,66 690,132 655,218 545,218 510,132" fill="#c9ecfd"/>
  <g fill="#15237f">
    <circle cx="600" cy="66" r="4"/><circle cx="690" cy="132" r="4"/><circle cx="655" cy="218" r="4"/><circle cx="545" cy="218" r="4"/><circle cx="510" cy="132" r="4"/>
  </g>
  <circle cx="560" cy="150" r="7" fill="#15237f"/>
  <text x="573" y="156" font-family="Open Sans, Arial, sans-serif" font-weight="600" font-size="15" fill="#15237f">quorbelline</text>
</svg>

<div class="abs tier" style="left:212px;top:2280px">0 – 5 % <small>net profit</small> &gt; 0%<span>performance fee</span></div>
<div class="abs tier" style="left:780px;top:2280px">&gt; 15% <small>net profit</small> &gt; 15%<span>performance fee</span></div>
<div class="abs tier" style="left:250px;top:2450px">5 – 10% <small>net profit</small> &gt; 5%<span>performance fee</span></div>
<div class="abs tier" style="left:746px;top:2450px">10-15 % <small>net profit</small> &gt; 13%<span>performance fee</span></div>
<p class="abs dist-note">The remainder (50% minus performance fee, so at least 35%) is reinvested</p>

<footer class="abs footer"></footer>
<h4 class="abs f-head" style="left:80px;top:2668px">For more info</h4>
<p class="abs f-text" style="left:80px;top:2706px;width:230px">Lorem Ipsum is simply dummy text of the printing and typesetting industry. Lorem Ipsum has been the industry's.</p>
<a class="abs btn" style="left:80px;top:2822px">Download PDF</a>

<h4 class="abs f-head" style="left:356px;top:2668px">Contact info</h4>
<svg class="abs" style="left:354px;top:2708px" width="22" height="30" viewBox="0 0 22 30" aria-hidden="true"><path d="M11 1C5.5 1 1 5.4 1 10.8 1 18 11 29 11 29s10-11 10-18.2C21 5.4 16.5 1 11 1z" fill="#fff"/><circle cx="11" cy="11" r="4" fill="#15237f"/></svg>
<div class="abs f-text" style="left:386px;top:2712px;font-weight:600;letter-spacing:1px">quorbelline</div>
<p class="abs f-text" style="left:386px;top:2756px;width:220px">Rooms 08-12, 9B/F., North Wing, Meridian Trade Centre, Lantern Quay, 42, Willow Road, Kowloon, Hong Kong.</p>

<h4 class="abs f-head" style="left:640px;top:2668px">Newsletter</h4>
<p class="abs f-text" style="left:640px;top:2706px;width:260px">Subscribe to Our Newsletter to get latest News &amp; Updates About Company</p>
<div class="abs newsletter-field">Enter Your E-Mail</div>
<div class="abs newsletter-send"><svg width="22" height="22" viewBox="0 0 24 24" aria-hidden="true"><path d="M2 11 22 3l-6 18-4-7-10-3z M12 14l10-11" fill="none" stroke="#15237f" stroke-width="1.8" stroke-linejoin="round"/></svg></div>

<div class="abs f-brand"><div class="f-brand-dot"></div><div class="f-brand-name">quorbelline</div></div>
<span class="abs social" style="left:957px"></span>
<span class="abs social" style="left:1009px"></span>
<span class="abs social" style="left:1061px"></span>

<div class="abs f-rule"></div>
<p class="abs copyright">© <strong>quorbelline</strong> - 2017. All Rights Reserved.</p>

</body>
</html>
```